Telecommunications/Power civil contractor needs business card design

Were a new telecommunications/power underground civil contractor that is looking for a new business card design. Our company colours are silver or grey and orange. Feel free to use the white background logo or the black background logo.

Target Market(s)

Local contractors, utility companies, private sector mining/energy companies, developers.

Industry/Entity Type

Telecommunications

Contact Information for Business Card

Each card will need the following info:
Persons name:
Title:
E-mail:
Phone number:
Shop Address:
Mailing Address:

Requirements
Must have
• Each card will need the following info:
• Persons name:
• Title:
• E-mail:
• Phone number:
• Shop Address:
• Mailing Address:

```html
<!DOCTYPE html>
<html lang="en">
<head>
<meta charset="utf-8">
<title>Ridgeline Civil Inc — Business Card</title>
<link rel="stylesheet" href="https://fonts.googleapis.com/css2?family=Roboto:wght@400;700&display=swap">
<style>
  :root {
    --stage: #3a3a3a;
    --card: #050505;
    --orange: #f26a2e;
    --silver: #9a9a9a;
    --text: #e6e6e6;
  }
  html, body {
    margin: 0;
    width: 1200px;
    height: 716px;
    overflow: hidden;
    background: var(--stage);
    font-family: "Roboto", Arial, sans-serif;
  }
  .canvas {
    position: relative;
    width: 1200px;
    height: 716px;
  }
  .card {
    position: absolute;
    top: 204px;
    width: 540px;
    height: 308px;
    background: var(--card);
    overflow: hidden;
    box-shadow: 0 6px 18px rgba(0,0,0,.45);
  }
  .card--front { left: 40px; }
  .card--back  { left: 620px; }

  .brand {
    position: absolute;
    display: flex;
    flex-direction: column;
    gap: 6px;
  }
  .brand__dot {
    border: 3px solid var(--orange);
    border-radius: 50%;
    box-sizing: border-box;
  }
  .brand__name {
    color: var(--orange);
    font-weight: 700;
    letter-spacing: .04em;
    text-transform: uppercase;
    line-height: 1;
    white-space: nowrap;
  }

  .card--front .brand { left: 30px; top: 22px; align-items: flex-start; }
  .card--front .brand__dot { width: 28px; height: 28px; }
  .card--front .brand__name { font-size: 14px; }

  .card--back .brand { right: 30px; bottom: 30px; align-items: flex-end; }
  .card--back .brand__dot { width: 46px; height: 46px; }
  .card--back .brand__name { font-size: 22px; }

  .feature-name {
    position: absolute;
    right: 30px;
    top: 112px;
    color: var(--silver);
    font-weight: 700;
    font-size: 32px;
    line-height: 1.1;
    letter-spacing: .04em;
    text-transform: uppercase;
    text-align: right;
  }

  .contact {
    position: absolute;
    left: 30px;
    top: 92px;
    color: var(--text);
    font-size: 12.5px;
    line-height: 1.5;
  }
  .contact__name { color: var(--orange); font-weight: 700; }
  .contact__address { margin-top: 10px; }
  .contact__lines { margin-top: 12px; }
  .contact__line {
    display: flex;
    align-items: center;
    gap: 8px;
  }
  .icon { width: 11px; height: 11px; fill: var(--orange); }
</style>
</head>
<body>
<main class="canvas">
  <section class="card card--front">
    <div class="brand">
      <span class="brand__dot"></span>
      <span class="brand__name">Ridgeline Civil Inc</span>
    </div>
    <div class="contact">
      <div class="contact__name">Dalton Reyes</div>
      <div class="contact__title">Managing Director</div>
      <div class="contact__address">N. 48 Quarry Road,<br>Suite 210, Boise, ID 83702</div>
      <div class="contact__lines">
        <div class="contact__line">
          <svg class="icon" viewBox="0 0 12 12" aria-hidden="true"><path d="M2.5 1 L4.5 1 L5.2 3.6 L4 4.6 C4.8 6.2 5.8 7.2 7.4 8 L8.4 6.8 L11 7.5 L11 9.5 C11 10.3 10.3 11 9.5 11 C5 11 1 7 1 2.5 C1 1.7 1.7 1 2.5 1 Z"/></svg>
          <span>208.555.0147</span>
        </div>
        <div class="contact__line">
          <svg class="icon" viewBox="0 0 12 12" aria-hidden="true"><path d="M1 2.5 H11 V9.5 H1 Z M1.8 3.2 L6 6.4 L10.2 3.2 Z" fill-rule="evenodd"/></svg>
          <span>office@ridgelinecivil.com</span>
        </div>
      </div>
    </div>
    <div class="feature-name">Ridgeline<br>Civil Inc</div>
  </section>

  <section class="card card--back">
    <div class="brand">
      <span class="brand__dot"></span>
      <span class="brand__name">Ridgeline Civil Inc</span>
    </div>
  </section>
</main>
</body>
</html>
```